Modern Business Card

Modern professional business card with more than just logo and demographic info. Something memorable.

We are a trendy/modern chiropractic group with an emphasis on neurology, hence the minimalist-type brain logo. We want to convey that modern and technical aspect with professionalism and the elite nature of our practice environment.

```html
<!DOCTYPE html>
<html lang="en">
<head>
<meta charset="utf-8">
<title>Clarion Chiropractic – Business Card</title>
<link rel="stylesheet" href="https://fonts.googleapis.com/css2?family=Quattrocento:wght@400&family=Fira+Sans+Condensed:wght@500&display=swap">
<style>
  :root {
    --backdrop: #b3b3b3;
    --brand-blue: #3e639d;
    --brand-blue-deep: #3a5e97;
    --card-white: #f3f3f3;
    --ink: #1d1d1d;
    --muted-ink: #3a3a3a;
    --paper-text: #f4f4f4;
    --faint-mark: rgba(255, 255, 255, 0.09);
  }
  html, body {
    margin: 0;
    padding: 0;
    overflow: hidden;
  }
  body {
    width: 1200px;
    height: 576px;
    background: var(--backdrop);
    position: relative;
    font-family: "Quattrocento", Georgia, serif;
  }
  .card {
    position: absolute;
    width: 484px;
    height: 292px;
    border-radius: 10px;
    box-sizing: border-box;
    overflow: hidden;
  }
  .card-front {
    left: 82px;
    top: 139px;
    background: linear-gradient(180deg, var(--brand-blue) 0%, var(--brand-blue-deep) 100%);
    color: var(--paper-text);
  }
  .card-back {
    left: 602px;
    top: 138px;
    background: var(--card-white);
    color: var(--ink);
  }
  .mark-shape {
    position: absolute;
    border-radius: 50%;
  }
  .card-front .mark-shape {
    width: 280px;
    height: 280px;
    left: 102px;
    top: 6px;
    background: var(--faint-mark);
  }
  .card-back .mark-shape {
    width: 206px;
    height: 206px;
    left: 272px;
    top: 43px;
    background: var(--brand-blue);
  }
  .wordmark {
    margin: 0;
    font-weight: 400;
    text-transform: uppercase;
    line-height: 1;
    position: absolute;
  }
  .wordmark span { display: block; }
  .card-front .wordmark {
    left: 0;
    right: 0;
    top: 100px;
    text-align: center;
  }
  .card-front .wordmark-main { font-size: 68px; letter-spacing: 1px; }
  .card-front .wordmark-sub { font-size: 39px; }
  .card-back .wordmark {
    left: 29px;
    top: 30px;
    color: var(--ink);
  }
  .card-back .wordmark-main { font-size: 44px; letter-spacing: 0.5px; }
  .card-back .wordmark-sub { font-size: 25px; margin-top: -2px; }
  .person-name {
    position: absolute;
    left: 29px;
    top: 112px;
    margin: 0;
    font-family: "Fira Sans Condensed", "Arial Narrow", sans-serif;
    font-weight: 500;
    font-size: 19px;
    color: var(--brand-blue);
  }
  .person-role {
    position: absolute;
    left: 29px;
    top: 139px;
    margin: 0;
    font-size: 12.5px;
    color: var(--muted-ink);
  }
  .contact-list {
    position: absolute;
    left: 29px;
    top: 176px;
    margin: 0;
    padding: 0;
    list-style: none;
    font-size: 12.5px;
    color: var(--muted-ink);
  }
  .contact-list li {
    display: flex;
    align-items: center;
    height: 18px;
  }
  .contact-icon {
    width: 12px;
    height: 12px;
    margin-right: 9px;
    fill: var(--brand-blue);
  }
  .address {
    position: absolute;
    left: 29px;
    top: 236px;
    margin: 0;
    font-style: normal;
    font-size: 12.5px;
    line-height: 18px;
    color: var(--muted-ink);
  }
</style>
</head>
<body>

  <section class="card card-front" aria-label="Card front">
    <div class="mark-shape" aria-hidden="true"></div>
    <h1 class="wordmark">
      <span class="wordmark-main">Clarion</span>
      <span class="wordmark-sub">Chiropractic</span>
    </h1>
  </section>

  <section class="card card-back" aria-label="Card back">
    <div class="mark-shape" aria-hidden="true"></div>
    <h2 class="wordmark">
      <span class="wordmark-main">Clarion</span>
      <span class="wordmark-sub">Chiropractic</span>
    </h2>

    <p class="person-name">Daniel Reed Carter</p>
    <p class="person-role">Managing Director</p>

    <ul class="contact-list">
      <li>
        <svg class="contact-icon" viewBox="0 0 12 12" aria-hidden="true">
          <path d="M1 4.5C1 3 2.5 2 6 2s5 1 5 2.5v1H8.5V4.2h-5v1.3H1z"/>
          <rect x="2.5" y="6" width="7" height="4.5" rx="1"/>
        </svg>
        555-010-2040
      </li>
      <li>
        <svg class="contact-icon" viewBox="0 0 12 12" aria-hidden="true">
          <path d="M1 2.5h10v7H1z M1.8 3.2 6 6.6l4.2-3.4" stroke="#f3f3f3" stroke-width="0.9"/>
        </svg>
        daniel@clarionchiro.com
      </li>
      <li>
        <svg class="contact-icon" viewBox="0 0 12 12" aria-hidden="true">
          <circle cx="6" cy="6" r="5"/>
          <path d="M1 6h10M6 1c-2.4 3-2.4 7 0 10M6 1c2.4 3 2.4 7 0 10" stroke="#f3f3f3" stroke-width="0.8" fill="none"/>
        </svg>
        www.clarionchiro.com
      </li>
    </ul>

    <address class="address">
      78 Maple Ave., Fairview,<br>
      Lakeside, US 104520
    </address>
  </section>

</body>
</html>
```